Roofing Contractor business card redesign

I want to redesign my business card with a fresh, eye catching concept

Target Market(s)

Residential Roofing Clients, potential employees, and subcontractors.

Industry/Entity Type

Business

Colors

Designer to choose colors to be used in the design.

Requirements
Nice to have
• I just want something that's more pleasing to the eye. You can use a combination of either / or of my logos.

```html
<!DOCTYPE html>
<html lang="en">
<head>
<meta charset="utf-8">
<title>Solid Crew General Contractors – Business Card</title>
<link rel="stylesheet" href="https://fonts.googleapis.com/css2?family=Oswald:wght@600&family=Open+Sans:wght@700&family=Roboto:wght@400;500&display=swap">
<style>
  :root {
    --bg: #ece8e3;
    --orange: #e8711e;
    --yellow: #f5c015;
    --brown: #4a1a10;
    --brown-dark: #3a140c;
    --card-white: #f4f4f3;
    --text-grey: #555555;
    --accent: #e8711e;
    --divider: #cfcfcf;
  }
  * { margin: 0; padding: 0; box-sizing: border-box; }
  html, body { width: 1200px; height: 960px; overflow: hidden; background: var(--bg); }
  .canvas { position: relative; width: 1200px; height: 960px; }

  .card {
    position: absolute;
    left: 320px;
    width: 598px;
    border-radius: 18px;
    overflow: hidden;
    box-shadow: 0 3px 8px rgba(0,0,0,0.18);
  }

  /* Front */
  .card-front {
    top: 95px;
    height: 360px;
    background: linear-gradient(100deg, var(--orange) 0%, var(--orange) 30%, var(--yellow) 30%, var(--yellow) 100%);
  }
  .front-emblem {
    position: absolute;
    left: 35px;
    top: 15px;
    width: 340px;
    height: 340px;
    border-radius: 50%;
    border: 6px solid #ffffff;
    background: radial-gradient(circle at 50% 40%, var(--orange) 0%, #b5501a 45%, var(--brown-dark) 100%);
  }
  .front-name {
    position: absolute;
    left: 380px;
    top: 236px;
    font-family: "Oswald", sans-serif;
    font-weight: 600;
    font-size: 44px;
    line-height: 1.1;
    color: var(--brown);
    letter-spacing: -0.5px;
  }
  .front-tagline {
    position: absolute;
    left: 382px;
    top: 292px;
    font-family: "Open Sans", sans-serif;
    font-weight: 700;
    font-size: 15px;
    color: var(--brown);
  }
  .front-web {
    position: absolute;
    left: 382px;
    top: 315px;
    font-family: "Roboto", sans-serif;
    font-size: 14px;
    letter-spacing: 2px;
    color: #6a5a4a;
  }

  /* Back */
  .card-back {
    top: 493px;
    height: 340px;
    background: var(--card-white);
  }
  .back-band {
    position: absolute;
    left: 0; right: 0; bottom: 0;
    height: 13px;
    background: var(--brown-dark);
    border-top: 3px solid var(--orange);
  }
  .back-logo {
    position: absolute;
    left: 50px;
    top: 138px;
    display: flex;
    align-items: center;
    gap: 8px;
  }
  .back-logo-name {
    font-family: "Oswald", sans-serif;
    font-weight: 600;
    font-size: 36px;
    line-height: 1;
    color: var(--brown);
  }
  .back-logo-dot {
    width: 34px;
    height: 34px;
    border-radius: 50%;
    background: var(--orange);
  }
  .back-tagline {
    position: absolute;
    left: 52px;
    top: 193px;
    font-family: "Open Sans", sans-serif;
    font-weight: 700;
    font-size: 16px;
    color: var(--brown);
  }
  .back-divider {
    position: absolute;
    left: 307px;
    top: 72px;
    width: 1px;
    height: 205px;
    background: var(--divider);
  }
  .contact {
    position: absolute;
    left: 332px;
    top: 74px;
    font-family: "Roboto", sans-serif;
  }
  .contact-name {
    font-weight: 500;
    font-size: 20px;
    color: var(--brown);
    letter-spacing: 0.3px;
  }
  .contact-role {
    font-size: 15px;
    line-height: 20px;
    color: var(--accent);
  }
  .contact-address {
    margin-top: 10px;
    font-size: 14px;
    line-height: 18px;
    color: var(--text-grey);
  }
  .contact-list { margin-top: 12px; list-style: none; }
  .contact-list li {
    display: flex;
    align-items: center;
    gap: 9px;
    font-size: 14px;
    line-height: 19px;
    color: var(--text-grey);
  }
  .contact-list svg { width: 12px; height: 12px; fill: var(--brown-dark); flex: none; }
</style>
</head>
<body>
<div class="canvas">

  <section class="card card-front">
    <div class="front-emblem" role="img" aria-label="Illustration of three smiling contractors with tools in front of a roof, inside a round badge"></div>
    <div class="front-name">Solid Crew</div>
    <div class="front-tagline">General Contractors, Inc.</div>
    <div class="front-web">www.solidcrewtx.com</div>
  </section>

  <section class="card card-back">
    <div class="back-logo">
      <span class="back-logo-name">Solid Crew</span>
      <span class="back-logo-dot"></span>
    </div>
    <div class="back-tagline">General Contractors, Inc.</div>
    <div class="back-divider"></div>

    <div class="contact">
      <div class="contact-name">DAN WHITMORE</div>
      <div class="contact-role">Certified Roof Inspector</div>
      <div class="contact-role">Licensed Property Adjuster</div>
      <div class="contact-address">4810 Linden Avenue Suite 110<br>Plano, TX 75093</div>
      <ul class="contact-list">
        <li>
          <svg viewBox="0 0 24 24"><path d="M6.6 10.8a15 15 0 0 0 6.6 6.6l2.2-2.2c.3-.3.7-.4 1-.2 1.1.4 2.3.6 3.6.6.6 0 1 .4 1 1V20c0 .6-.4 1-1 1A17 17 0 0 1 3 4c0-.6.4-1 1-1h3.5c.6 0 1 .4 1 1 0 1.3.2 2.5.6 3.6.1.3 0 .7-.2 1z"/></svg>
          (555) 014-2200
        </li>
        <li>
          <svg viewBox="0 0 24 24"><path d="M7 1h10a2 2 0 0 1 2 2v18a2 2 0 0 1-2 2H7a2 2 0 0 1-2-2V3a2 2 0 0 1 2-2zm0 3v14h10V4zm5 15.5a1.2 1.2 0 1 0 0 2.4 1.2 1.2 0 0 0 0-2.4z"/></svg>
          (555) 017-3391
        </li>
        <li>
          <svg viewBox="0 0 24 24"><path d="M2 5h20v14H2zm2 2v.5l8 5 8-5V7zm0 2.8V17h16V9.8l-8 5z"/></svg>
          dan@solidcrewtx.com
        </li>
        <li>
          <svg viewBox="0 0 24 24"><path d="M12 2a10 10 0 1 0 0 20 10 10 0 0 0 0-20zm-1 17.9A8 8 0 0 1 4.1 11H7c.1 1 .5 2 1.2 2.6L11 15zm6.9-2.7c-.3-.8-1-1.2-1.9-1.2h-1v-3c0-.6-.4-1-1-1H8V10h2c.6 0 1-.4 1-1V7h2a2 2 0 0 0 2-2v-.4a8 8 0 0 1 2.9 12.6z"/></svg>
          www.solidcrewtx.com
        </li>
      </ul>
    </div>

    <div class="back-band"></div>
  </section>

</div>
</body>
</html>
```